Redesign Craft Brewing Recipe Website

Originally built with Bootstrap just to get the site going, I am seeking a complete redesign of the sites home page and recipe page. I am an experienced web developer with no graphic background, initially just looking for psd mocks.

I prefer styles that are clean and modern, and would prefer anything that is fun, engaging, and has an organic feel to it. I currently have a cartoon rabbit as a logo, but it needs some modification/tweaking, so any help in that area would be great as well.

Current site:
http://velvetfinch.cloudpagehost.net/

Current launch page/logo:
http://www.velvetfinch.com/

I like the overall layout of the elements currently, but the design sucks.

The launch page is at the following URL

Reason: Still looking for a more modern design. Designs received so far are too similar to the original.

My site is content based and does not contain images or products. Your design should not consist of large images.

Reason: The website has very little images, so the designs need to be more text and content based. The header needs to be very small and should not contain an ad rotater.

Target Market(s)

Home brewers, Craft brewers, Microbreweries, Brewpubs

Requirements
Must have
• Web 2.0 Look and Feel, Fun, Hip, Focus on content
Should not have
• A large photo as a header

```html
<!DOCTYPE html>
<html lang="en">
<head>
<meta charset="utf-8">
<title>VelvetFinch – Home</title>
<link rel="stylesheet" href="https://fonts.googleapis.com/css2?family=Oswald:wght@400;500&family=Open+Sans:wght@400;600;700&display=swap">
<style>
:root{
  --ink:#2b2b2b;
  --red:#d43b36;
  --red-dark:#b8302c;
  --accent:#c0261f;
  --nav:#f7c96a;
  --nav-edge:#e9a63a;
  --blue:#34a6e0;
  --bubble:#5bbcf0;
  --card:#eef2f5;
  --card-edge:#d9e1e7;
  --muted:#9aa3ab;
  --text:#7c848b;
  --footer:#1b1b1b;
  --bar:#2e2e2e;
  --link:#f0b400;
}
*{box-sizing:border-box;margin:0;padding:0}
html,body{width:761px;height:1200px;overflow:hidden}
body{position:relative;background:#fbfbfb;font-family:"Open Sans",Arial,sans-serif;color:var(--ink)}
.abs{position:absolute}

/* header */
.site-header{left:0;top:0;width:761px;height:68px;background:linear-gradient(#363636,#222)}
.brand{left:82px;top:18px;display:flex;align-items:center;gap:8px;font-family:"Oswald",sans-serif;font-weight:500;font-size:25px;color:#f2b33d;letter-spacing:.5px}
.brand-mark{width:28px;height:28px;border-radius:50%;background:#f4f4f4}
.main-nav{left:380px;top:30px;width:298px;height:26px;border-radius:3px;background:linear-gradient(#fbd98a,var(--nav));border:1px solid var(--nav-edge);display:flex;justify-content:space-around;align-items:center;font-size:8.5px;color:#4a3510}

/* featured intro (text only) */
.hero{left:0;top:68px;width:761px;height:306px;background:linear-gradient(#e0463f,var(--red-dark))}
.hero-card{left:82px;top:88px;width:596px;height:246px;background:#fff;border-radius:2px;box-shadow:0 1px 3px rgba(0,0,0,.3)}
.hero-copy{left:108px;top:110px;width:544px}
.hero-kicker{font-size:8px;font-weight:700;letter-spacing:1.5px;color:var(--accent);text-transform:uppercase;margin-bottom:6px}
.hero-title{font-family:"Oswald",sans-serif;font-weight:400;font-size:26px;line-height:30px;color:#222;text-transform:uppercase;padding-bottom:10px;border-bottom:1px dashed #ddd}
.hero-title span{color:var(--accent)}
.hero-meta{font-size:8px;color:var(--muted);padding:9px 0 10px;border-bottom:1px dashed #ddd}
.hero-meta b{font-weight:400;color:#333}
.hero-cols{display:flex;gap:28px;margin-top:14px}
.hero-text{flex:1;font-size:8.5px;line-height:14px;color:var(--text)}
.btn-dark{display:inline-block;background:linear-gradient(#444,#222);color:#fff;font-size:8.5px;border-radius:3px;letter-spacing:.5px}
.learn-more{left:108px;top:292px;width:83px;height:24px;line-height:24px;text-align:center}

/* recipes bar */
.section-bar{left:82px;top:398px;width:596px;height:31px;border-radius:3px;background:linear-gradient(#444,#262626);color:#fff;display:flex;align-items:center}
.section-bar h2{font-family:"Oswald",sans-serif;font-weight:500;font-size:14px;margin:0 58px 0 13px}
.section-bar nav{font-size:9px;display:flex;gap:22px}

/* filter */
.filter{left:82px;top:447px;width:147px;height:359px;background:#f2f3f4;border:1px solid #e2e4e6;border-radius:3px}
.filter-head{height:27px;background:var(--blue);color:#fff;font-family:"Oswald",sans-serif;font-size:10px;line-height:27px;padding-left:10px;border-radius:3px 3px 0 0}
.pill{position:absolute;left:8px;width:130px;height:18px;border:1px solid #ddd;border-radius:9px;background:#fff;font-size:7.5px;line-height:16px;padding-left:12px;color:#555}
.pill .tail{position:absolute;right:3px;top:2px;width:12px;height:12px;border-radius:50%;border:1px solid #ccc;font-size:6px;line-height:10px;text-align:center;color:#333;font-weight:700}
.filter-label{position:absolute;left:14px;font-size:10px;color:#555}
.range-label{position:absolute;left:20px;top:117px;font-size:7.5px;color:#555}
.range{position:absolute;left:8px;top:130px;width:130px;height:16px;border-radius:8px;background:#fff;border:1px solid #ddd}
.range::before{content:"";position:absolute;left:12px;right:12px;top:6px;height:3px;background:#cfe5f2;border-radius:2px}
.range i{position:absolute;top:2px;width:10px;height:10px;border-radius:50%;background:#fff;border:1px solid #aaa}
.ticks{position:absolute;left:22px;top:149px;width:106px;display:flex;justify-content:space-between;font-size:6px;color:#666}
.divider{position:absolute;left:0;top:294px;width:145px;border-top:1px solid #e0e0e0}
.update{position:absolute;left:29px;top:322px;width:87px;height:20px;line-height:20px;text-align:center;font-family:"Oswald",sans-serif;font-size:8.5px}

/* cards */
.card{position:absolute;width:214px;height:156px;background:var(--card);border:1px solid var(--card-edge);display:flex}
.card-media{width:107px;height:100%;background:#fff;position:relative;border-right:1px solid var(--card-edge)}
.card-media .art{position:absolute;left:8px;right:8px;top:10px;bottom:30px;border-radius:2px}
.tags{position:absolute;left:0;right:0;bottom:0;height:22px;background:#2a2a2a;display:flex;font-family:"Oswald",sans-serif;font-size:7px;color:#fff;align-items:center}
.tags span{flex:1;text-align:center;white-space:nowrap}
.tags span+span{border-left:1px solid #555}
.card-body{padding:12px 6px 0 9px;flex:1;position:relative}
.card-body h3{font-weight:400;font-size:10px;line-height:11.5px;color:#333;height:24px}
.card-body .by{font-size:7px;color:#aab;margin:4px 0 8px}
.card-body .by b{font-weight:400;color:#444}
.card-body p{font-size:6.4px;line-height:11.5px;color:#9aa0a6}
.stats{position:absolute;left:6px;bottom:8px;display:flex;gap:4px}
.stats i{width:21px;height:21px;border-radius:50%;background:var(--bubble);color:#fff;font-style:normal;font-size:5.5px;line-height:6.5px;text-align:center;padding-top:4px;border:1px solid #fff;box-shadow:0 0 0 1px #b7dff5}

/* footer */
.torn{left:0;top:962px;width:761px;height:32px;background:linear-gradient(#fbfbfb,#eee)}
.site-footer{left:0;top:994px;width:761px;height:172px;background:var(--footer)}
.footer-col{position:absolute;top:1014px}
.footer-col h4{position:relative;height:22px;width:191px;background:#000;color:#fff;font-family:"Oswald",sans-serif;font-weight:400;font-size:13px;line-height:22px;padding-left:6px;text-transform:uppercase;white-space:nowrap}
.footer-col h4::after{content:"";position:absolute;left:18px;bottom:-5px;border:5px solid transparent;border-bottom:0;border-top-color:#000}
.welcome{left:69px;top:1008px;width:188px;height:146px;background:#000}
.welcome-text{left:83px;top:1059px;width:160px;font-size:8px;line-height:14px;color:#fff}
.tweet{font-size:7.8px;line-height:12px;color:#ccc;margin-top:9px}
.tweet b{color:var(--link);font-weight:400}
.tweet em{display:block;color:#888;font-size:6.5px;margin-top:2px}
.popular-thumb{left:483px;top:1064px;width:90px;height:62px;border:2px solid #fff;background:linear-gradient(90deg,#c7b26b,#b63a3a,#e8e2c8,#d55a7a,#6a9e4a)}
.popular-text{left:581px;top:1066px;width:95px}
.popular-text h5{font-family:"Oswald",sans-serif;font-weight:400;font-size:10.5px;line-height:14px;color:#fff}
.popular-text p{font-size:7px;color:#888;margin-top:6px;line-height:10px}
.popular-text p b{font-weight:400;color:var(--link)}
.copy-bar{left:0;top:1166px;width:761px;height:34px;background:var(--bar);font-size:7.5px;color:#ddd}
.copy-bar .legal{position:absolute;left:83px;top:12px}
.copy-bar nav{position:absolute;right:83px;top:12px;display:flex;gap:9px}
</style>
</head>
<body>

<header class="site-header abs">
  <div class="brand abs"><span class="brand-mark"></span>VELVETFINCH</div>
  <nav class="main-nav abs"><span>HOME</span><span>RECIPES</span><span>ABOUT US</span><span>OUR CLIENTS</span><span>CONTACT</span></nav>
</header>

<section class="hero abs"></section>
<div class="hero-card abs"></div>
<div class="hero-copy abs">
  <div class="hero-kicker">Featured recipe</div>
  <h1 class="hero-title">Lorem ipsum spémen <span>impression</span></h1>
  <div class="hero-meta">By <b>Elmer Voss</b> at <b>15/3/2013</b></div>
  <div class="hero-cols">
    <p class="hero-text">Le Lorem Ipsum est simplement du faux texte employé dans la composition et la mise en page avant impression. Le Lorem Ipsum est le faux texte standard de l'imprimerie depuis.</p>
    <p class="hero-text">Quand un peintre anonyme assembla ensemble des morceaux de texte pour réaliser un livre spécimen de polices de texte.</p>
  </div>
</div>
<a class="btn-dark learn-more abs">LEARN MORE</a>

<div class="section-bar abs">
  <h2>LATEST RECIPES</h2>
  <nav><span>All</span><span>|</span><span>Recent</span><span>|</span><span>Popular</span></nav>
</div>

<aside class="filter abs">
  <div class="filter-head">WINE RECIPES FILTER</div>
  <div class="pill" style="top:38px;color:#aaa">Stout<span class="tail">GO</span></div>
  <div class="filter-label" style="top:66px">Match Maker</div>
  <div class="pill" style="top:90px">Boil Size<span class="tail" style="color:var(--blue)">●</span></div>
  <div class="range-label">0 Gals to 25 Gals</div>
  <div class="range"><i style="left:36px"></i><i style="left:102px"></i></div>
  <div class="ticks"><span>0</span><span>5</span><span>10</span><span>15</span><span>20</span><span>25</span></div>
  <div class="filter-label" style="top:180px">Brewing</div>
  <div class="pill" style="top:196px">Extract<span class="tail">▾</span></div>
  <div class="filter-label" style="top:235px">Styles</div>
  <div class="pill" style="top:251px">American Amber Ale<span class="tail">▾</span></div>
  <div class="divider"></div>
  <a class="btn-dark update">UPDATE SEARCH</a>
</aside>

<article class="card" style="left:241px;top:447px">
  <div class="card-media"><div class="art" role="img" aria-label="Three wine bottles in green, red and dark glass" style="background:linear-gradient(90deg,#6a7a3a,#b8334a,#3a2a30)"></div><div class="tags"><span>Extract</span><span>Sweet Mead</span></div></div>
  <div class="card-body"><h3>Oak Bastard Sweet Mead</h3><div class="by">created by <b>Hollis Crane</b></div><p>Lorem ipsum dolor sit amet, consectetur adipisicing elit, sed do eiusmod tempor dunt ut labore et dolore magna aliqua.</p>
  <div class="stats"><i>2.24%<br>abv</i><i>24<br>ibu</i><i>1.006<br>fb</i><i>1.022<br>og</i></div></div>
</article>
<article class="card" style="left:464px;top:447px">
  <div class="card-media"><div class="art" role="img" aria-label="Two wine bottles, one dark red and one golden" style="background:linear-gradient(90deg,#5a1a1a,#c63a2a,#d8b830)"></div><div class="tags"><span>Extract</span><span>Sweet Stout</span></div></div>
  <div class="card-body"><h3>Moon Man Sweet Stout</h3><div class="by">created by <b>Hollis Crane</b></div><p>Lorem ipsum dolor sit amet, consectetur adipisicing elit, sed do eiusmod tempor dunt ut labore et dolore magna aliqua.</p>
  <div class="stats"><i>2.24%<br>abv</i><i>24<br>ibu</i><i>1.006<br>fb</i><i>1.022<br>og</i></div></div>
</article>
<article class="card" style="left:241px;top:618px">
  <div class="card-media"><div class="art" role="img" aria-label="Three wine bottles in dark, red and pale glass" style="background:linear-gradient(90deg,#2a1a1a,#c02a2a,#e8e2a8)"></div><div class="tags"><span>Extract</span><span>Dunkelweizen</span></div></div>
  <div class="card-body"><h3>Capitol Dunkelweizen</h3><div class="by">created by <b>Hollis Crane</b></div><p>Lorem ipsum dolor sit amet, consectetur adipisicing elit, sed do eiusmod tempor dunt ut labore et dolore magna aliqua.</p>
  <div class="stats"><i>13.93<br>abv</i><i>126<br>ibu</i><i>1.036<br>fb</i><i>1.139<br>og</i></div></div>
</article>
<article class="card" style="left:464px;top:618px">
  <div class="card-media"><div class="art" role="img" aria-label="Three wine bottles in pale, golden and dark red glass" style="background:linear-gradient(90deg,#c8c890,#b8b050,#5a2028)"></div><div class="tags"><span>Extract</span><span>Traditional Bock</span></div></div>
  <div class="card-body"><h3>Honeysucker Traditional Bock</h3><div class="by">created by <b>Hollis Crane</b></div><p>Lorem ipsum dolor sit amet, consectetur adipisicing elit, sed do eiusmod tempor dunt ut labore et dolore magna aliqua.</p>
  <div class="stats"><i>13.93<br>abv</i><i>126<br>ibu</i><i>1.036<br>fb</i><i>1.139<br>og</i></div></div>
</article>
<article class="card" style="left:241px;top:790px">
  <div class="card-media"><div class="art" role="img" aria-label="Two wine bottles, one pale and one dark" style="background:linear-gradient(90deg,#d8d098,#3a2a2a)"></div><div class="tags"><span>PartialMash</span><span>Baltic Porter</span></div></div>
  <div class="card-body"><h3>Venom<br>Baltic Porter</h3><div class="by">created by <b>Hollis Crane</b></div><p>Lorem ipsum dolor sit amet, consectetur adipisicing elit, sed do eiusmod tempor dunt ut labore et dolore magna aliqua.</p>
  <div class="stats"><i>13.93<br>abv</i><i>126<br>ibu</i><i>1.036<br>fb</i><i>1.139<br>og</i></div></div>
</article>
<article class="card" style="left:464px;top:790px">
  <div class="card-media"><div class="art" role="img" aria-label="Two wine bottles, one black and one pink" style="background:linear-gradient(90deg,#1a1a1a,#d890a8)"></div><div class="tags"><span>AllGrain</span><span>Munich Helles</span></div></div>
  <div class="card-body"><h3>Capitol<br>Munich Helles</h3><div class="by">created by <b>Hollis Crane</b></div><p>Lorem ipsum dolor sit amet, consectetur adipisicing elit, sed do eiusmod tempor dunt ut labore et dolore magna aliqua.</p>
  <div class="stats"><i>2.24%<br>abv</i><i>24<br>ibu</i><i>1.006<br>fb</i><i>1.022<br>og</i></div></div>
</article>

<div class="torn abs"></div>
<footer class="site-footer abs"></footer>
<div class="welcome abs"></div>
<div class="footer-col" style="left:78px"><h4>Welcome to VelvetFinch</h4></div>
<p class="welcome-text abs">Le Lorem Ipsum est simplement du faux texte employé dans la composition et la mise en page avant impression. Le Lorem Ipsum est le faux texte standard de l'imprimerie depuis.</p>

<div class="footer-col" style="left:282px">
  <h4>Latest tweets</h4>
  <div style="width:175px;padding-top:4px">
    <p class="tweet"><b>@reed_mallow</b> well, this looks cool. drops an e-mail so we can talk in person.<em>2 minutes ago</em></p>
    <p class="tweet"><b>@reed_mallow</b> well, this looks cool. drops an e-mail so we can talk in person.<em>2 minutes ago</em></p>
  </div>
</div>

<div class="footer-col" style="left:483px"><h4>Most popular post right now</h4></div>
<div class="popular-thumb abs" role="img" aria-label="Row of colourful wine bottles"></div>
<div class="popular-text abs">
  <h5>LE LOREM<br>IPSUM SIMPLEMENT</h5>
  <p>By <b>Dana Whitlock</b><br>at <b>15/3/2013</b></p>
</div>

<div class="copy-bar abs">
  <span class="legal">Copyright 2012 Website Name. All Rights Reserved.</span>
  <nav><span>Home</span><span>|</span><span>Recipes</span><span>|</span><span>About us</span><span>|</span><span>Our Clients</span><span>|</span><span>Contact</span></nav>
</div>

</body>
</html>
```